Road Construction Company needs business cards

We would like a new business card designed for our business.

We're a road construction company based in Qld, Australia.

Can the business card please have the following information on it.

Name: Warren Halbeck
Position: General Manager
Phone: 0472 915 348
Email: Warren.halbeck@tovrin.com.au
Address: 87 Marrow Ave, Pendlebay, QLD, 4023
Website: www.tovrin.com.au

Visually we'd like the card to be professional and simple.

Attached is our logo.

Our website is www.tovrin.com.au

Target Market(s)

Men aged 25-60

Contact Information for Business Card

As listed in project description

Font styles to use
Serif

Requirements
Must have
• Large logo on back of card

```html
<!DOCTYPE html>
<html lang="en">
<head>
<meta charset="utf-8">
<title>Tovrin – Business Card</title>
<link href="https://fonts.googleapis.com/css2?family=Open+Sans:wght@400;600;800&display=swap" rel="stylesheet">
<style>
  :root{
    --page:#e9e6e1;
    --card-blue:#1357a6;
    --card-dark:#222226;
    --ink-black:#0c0c0e;
    --accent:#1f78c9;
    --accent-light:#3d9be0;
    --rule:#1f6fc4;
    --text-light:#ffffff;
  }
  *{margin:0;padding:0;box-sizing:border-box}
  html,body{width:1200px;height:780px;overflow:hidden}
  body{
    background:var(--page);
    font-family:"Open Sans",Arial,sans-serif;
    position:relative;
  }
  .card{
    position:absolute;top:95px;
    width:350px;height:590px;border-radius:30px;
    box-shadow:0 10px 24px rgba(0,0,0,.25);
    overflow:hidden;
  }
  /* front */
  .card-front{left:215px;background:var(--card-blue)}
  .front-wordmark{
    position:absolute;left:50%;top:50%;
    transform:translate(-50%,-50%) rotate(-90deg);
    font-weight:800;font-size:124px;letter-spacing:6px;
    color:var(--ink-black);white-space:nowrap;line-height:1;
  }
  /* back */
  .card-back{left:635px;background:var(--card-dark);color:var(--text-light);text-align:center}
  .back-wordmark{
    position:absolute;top:70px;left:0;right:0;
    font-weight:800;font-size:46px;letter-spacing:3px;color:var(--accent);
  }
  .contact-block{position:absolute;left:0;right:0;top:296px}
  .person-name{font-weight:800;font-size:25px;color:var(--accent-light);letter-spacing:.5px;text-transform:uppercase}
  .person-role{font-weight:600;font-size:15px;margin-top:2px}
  .divider{
    display:flex;align-items:center;gap:10px;
    width:290px;margin:10px auto;
  }
  .divider::before,.divider::after{
    content:"";flex:1;height:1px;background:var(--rule);
  }
  .divider-plain{width:290px;height:1px;background:var(--rule);margin:12px auto 0}
  .icon{display:block}
  .contact-line{font-size:13.5px;line-height:1.45}
  .address{font-size:14px;line-height:1.45;margin-top:2px}
</style>
</head>
<body>

<section class="card card-front" aria-label="Card front">
  <div class="front-wordmark">TOVRIN</div>
</section>

<section class="card card-back" aria-label="Card back">
  <div class="back-wordmark">TOVRIN</div>

  <div class="contact-block">
    <div class="person-name">Warren Halbeck</div>
    <div class="person-role">General Manager</div>

    <div class="divider">
      <svg class="icon" width="90" height="26" viewBox="0 0 90 26" aria-hidden="true">
        <g fill="#1f6fc4">
          <circle cx="13" cy="13" r="12"/><circle cx="45" cy="13" r="12"/><circle cx="77" cy="13" r="12"/>
        </g>
        <path d="M8 7c-2 4 2 10 8 12l2-3-3-2-1 1c-2-1-3-3-4-5l1-1-2-3z" fill="#fff"/>
        <g fill="none" stroke="#fff" stroke-width="1.5" stroke-linecap="round">
          <rect x="38" y="8.5" width="14" height="10" rx="1"/><path d="M38 8.5l7 6 7-6"/>
          <circle cx="77" cy="13" r="6.5"/><path d="M70.5 13h13M77 6.5c-3 4-3 9 0 13M77 6.5c3 4 3 9 0 13"/>
        </g>
      </svg>
    </div>

    <div class="contact-line">0472 915 348</div>
    <div class="contact-line">www.tovrin.com.au</div>
    <div class="contact-line">Warren.halbeck@tovrin.com.au</div>

    <div class="divider">
      <svg class="icon" width="20" height="24" viewBox="0 0 20 24" aria-hidden="true">
        <g fill="none" stroke="#fff" stroke-width="1.6">
          <path d="M10 22c-4-5-6-8-6-11a6 6 0 0 1 12 0c0 3-2 6-6 11z"/><circle cx="10" cy="11" r="2"/>
        </g>
      </svg>
    </div>

    <div class="address">87 Marrow Ave,<br>Pendlebay, QLD, 4023</div>

    <div class="divider-plain"></div>
  </div>
</section>

</body>
</html>
```